Marlowby Services Website Design

We have most content but require a professional design. We have a logo already and will need it utilized along with several of the photos from the attached documentation.
First page should have our mission and Vision and the synapsis provided in the word document. Visitors will be prompted to select from one of our 3 divisions from this page.
Each division will have the same list of tabs : About, Services, Safety, Careers and Contact.
Photos on each divisions page should be representative of the divisions offerings. The word doc attached contains the requested content and we are open to edits that would complement and fill the website.
I like the Quorvane site www.quorvane.example - they are our competition so cant be modeled directly after this.
Please include prompts to request quote at each service page. align the format of the geotechnical page to the other 2 divisions.
I used chat gpt for some of the content so will need it optimized for SCO.

```html
<!DOCTYPE html>
<html lang="en">
<head>
<meta charset="UTF-8">
<title>Marlowby Services</title>
<link href="https://fonts.googleapis.com/css2?family=Michroma&family=Montserrat:wght@400;500;600&display=swap" rel="stylesheet">
<style>
  :root {
    --red: #ec1c24;
    --ink: #1e1e1e;
    --body: #555555;
    --panel: #efefef;
    --white: #ffffff;
    --rule: #e0434a;
  }
  * { margin: 0; padding: 0; box-sizing: border-box; }
  html, body { width: 1200px; height: 2253px; overflow: hidden; background: var(--white); }
  body { position: relative; font-family: "Montserrat", sans-serif; color: var(--ink); }

  .site-header { position: absolute; top: 0; left: 0; width: 1200px; height: 88px; background: var(--white); box-shadow: 0 1px 4px rgba(0,0,0,.06); z-index: 3; }
  .brand { position: absolute; left: 112px; top: 24px; font-family: "Michroma", sans-serif; font-size: 30px; letter-spacing: 1px; color: var(--red); }
  .main-nav { position: absolute; right: 111px; top: 30px; display: flex; gap: 32px; font-size: 17px; font-weight: 500; }
  .main-nav a { color: var(--ink); text-decoration: none; }

  .hero { position: absolute; top: 88px; left: 0; width: 1200px; height: 620px; }
  .hero svg { position: absolute; top: 0; left: 0; }
  .hero-title { position: absolute; top: 225px; left: 0; width: 1200px; text-align: center; color: var(--white); font-family: "Michroma", sans-serif; }
  .hero-title .kicker { display: block; font-size: 28px; letter-spacing: 1px; }
  .hero-title .name { display: block; font-size: 56px; letter-spacing: 2px; margin-top: 4px; }

  .section-heading { font-family: "Michroma", sans-serif; font-size: 38px; color: var(--red); font-weight: 400; letter-spacing: .5px; }
  .section-copy { font-size: 15.5px; line-height: 25.7px; color: var(--body); text-align: justify; }

  .vision .section-heading { position: absolute; left: 110px; top: 780px; }
  .vision .section-copy { position: absolute; left: 110px; top: 842px; width: 490px; }
  .frame { position: absolute; background: var(--white); box-shadow: 0 2px 14px rgba(0,0,0,.12); }
  .photo { position: absolute; }
  .vision .frame { left: 898px; top: 790px; width: 191px; height: 300px; }
  .vision .photo { left: 687px; top: 804px; width: 375px; height: 272px; background: linear-gradient(135deg, #2c2438 0%, #5a4654 55%, #a88f88 100%); }

  .divider { position: absolute; left: 214px; top: 1134px; width: 771px; height: 1px; background: var(--rule); }

  .mission .frame { left: 110px; top: 1175px; width: 191px; height: 300px; }
  .mission .photo { left: 137px; top: 1190px; width: 375px; height: 272px; background: linear-gradient(135deg, #bdb3a6 0%, #e2ddd6 55%, #f3f1ee 100%); }
  .mission .section-heading { position: absolute; left: 599px; top: 1166px; }
  .mission .section-copy { position: absolute; left: 599px; top: 1228px; width: 490px; }

  .divisions { position: absolute; top: 1563px; left: 0; width: 1200px; height: 622px; background: radial-gradient(circle at 20% 30%, #f4f4f4 0, var(--panel) 40%), var(--panel); }
  .divisions .section-heading { position: absolute; top: 76px; width: 1200px; text-align: center; font-size: 42px; }
  .division-card { position: absolute; top: 164px; width: 299px; }
  .division-card .thumb { width: 299px; height: 293px; }
  .division-card h3 { font-size: 25px; font-weight: 600; color: var(--ink); margin-top: 14px; letter-spacing: .3px; }
  .division-card a { display: inline-block; margin-top: 4px; font-size: 17px; color: var(--red); text-decoration: underline; text-underline-offset: 3px; }
  .card-aerial { left: 112px; }
  .card-aerial .thumb { background: linear-gradient(180deg, #3b78c9 0%, #7aa6d8 55%, #9a9690 75%, #7b7872 100%); }
  .card-drilling { left: 452px; }
  .card-drilling .thumb { background: linear-gradient(160deg, #9e9c98 0%, #b9b6b1 50%, #8d9a6c 100%); }
  .card-renewable { left: 791px; }
  .card-renewable .thumb { background: linear-gradient(200deg, #1f5fb8 0%, #3b7fd6 60%, #5c97e0 100%); }

  .site-footer { position: absolute; top: 2185px; left: 0; width: 1200px; height: 68px; background: var(--red); color: var(--white); text-align: center; font-size: 16px; font-weight: 600; line-height: 68px; }
</style>
</head>
<body>
  <header class="site-header">
    <div class="brand">MARLOWBY</div>
    <nav class="main-nav">
      <a href="#">Home</a><a href="#">About</a><a href="#">Services</a><a href="#">Safety</a><a href="#">Contact</a>
    </nav>
  </header>

  <section class="hero">
    <svg width="1200" height="620" viewBox="0 0 1200 620" role="img" aria-label="Photo of a white aerial lift truck with an extended boom parked on a dirt lot, darkened behind the welcome title">
      <defs>
        <linearGradient id="heroShade" x1="0" y1="0" x2="1" y2="1">
          <stop offset="0" stop-color="#4a4640"/>
          <stop offset=".5" stop-color="#3a3835"/>
          <stop offset="1" stop-color="#2a2a2a"/>
        </linearGradient>
      </defs>
      <path d="M78,528 Q620,705 1200,506 L1200,520 Q600,650 0,505 Z" fill="var(--red)"/>
      <path d="M0,0 H1200 V509 Q600,645 0,509 Z" fill="url(#heroShade)"/>
    </svg>
    <h1 class="hero-title"><span class="kicker">WELCOME TO</span><span class="name">MARLOWBY</span></h1>
  </section>

  <section class="vision">
    <h2 class="section-heading">Our Vision</h2>
    <p class="section-copy">To be the leading provider of aerial access, geotechnical drilling, and service solutions, setting the standard for excellence in safety, efficiency, and environmental stewardship.</p>
    <div class="frame"></div>
    <div class="photo" role="img" aria-label="Close-up of a compass dial with the needle pointing to the word vision"></div>
  </section>

  <div class="divider"></div>

  <section class="mission">
    <div class="frame"></div>
    <div class="photo" role="img" aria-label="Close-up of a golden compass needle pointing to the word mission"></div>
    <h2 class="section-heading">Our Mission</h2>
    <p class="section-copy">At Marlowby, our mission is to deliver unparalleled aerial access, geotechnical drilling, and service and maintenance solutions, consistently exceeding our clients' expectations. We strive to achieve this by investing in cutting-edge technology, fostering a culture of safety and continuous improvement, and prioritizing environmental sustainability. Through collaboration, integrity, and dedication, we aim to contribute to the success of our client while maintaining the highest standards of quality and professionalism.</p>
  </section>

  <section class="divisions">
    <h2 class="section-heading">Select Division</h2>
    <article class="division-card card-aerial">
      <div class="thumb" role="img" aria-label="Aerial lift truck parked beside a tall water tower under a blue sky"></div>
      <h3>Aerial Access</h3>
      <a href="#">Learn More</a>
    </article>
    <article class="division-card card-drilling">
      <div class="thumb" role="img" aria-label="Overhead view of a lift boom and work platform above a paved site"></div>
      <h3>Geotechnical Drilling</h3>
      <a href="#">Learn More</a>
    </article>
    <article class="division-card card-renewable">
      <div class="thumb" role="img" aria-label="Lift boom reaching up toward a wind turbine against a clear blue sky"></div>
      <h3>Renewable Energy</h3>
      <a href="#">Learn More</a>
    </article>
  </section>

  <footer class="site-footer">© 2024 Marlowby. All Rights Reserved&nbsp; | &nbsp;Privacy Policy&nbsp; | &nbsp;Terms Of Service</footer>
</body>
</html>
```